Brightfield Homes needs a web design and brand identifier

Brightfield Homes is a pioneering approach by Victorian councils and four greenhouse alliances to support low income households to install solar systems with no upfront costs.

Brightfield Homes will commence in May 2017.

Brightfield Homes is looking for a designer to create a website banner incorporating a brand identifier for Brightfield Homes. The brand identifier will be used in Brightfield Homes promotional materials, such as flyers and mail outs.

The website banner and brand identifier should engender trust and confidence in the target group (retirees).

Reason: Hi, Thank you for your work so far. We've been given advice to get a separate logo designed (instead of trying to include this as part of the banner design). Sorry for not realising this until now - we're new to all this. So, I have a couple of preliminary logo designs that are being considered by our project control group. I will forward a copy of the logo once we have it. The project control group is looking for a web design that is unique to Brightfield Homes and a design that draws on the key elements of the program (i.e. it helps people save money and take control). The site should be friendly but not too informal as the target group is seniors. Here's a link to another community energy organisation: www.kindlewattnet.com.au/ Apologies again for the delays. Cheers, Doug

Target Market(s)

Home owning, low income, retirees

Industry/Entity Type

Non Profit

Number of Pages Required

1 page

Font styles to use
Sans Serif

Requirements
Must have
• Use of Brightfield Home name
• Must promote Brightfield Homes as safe, reliable and trustworthy
Nice to have
• Blue - to engender sense of safety and confidence (open to suggestions, though)
• Solar panels / the sun
Should not have
• Anything that is hard to read
• anything that promotes riskyness

```html
<!DOCTYPE html>
<html lang="en">
<head>
<meta charset="utf-8">
<title>Brightfield Homes</title>
<link href="https://fonts.googleapis.com/css2?family=Source+Sans+3:wght@400;600;700&family=Open+Sans:wght@400;600&display=swap" rel="stylesheet">
<style>
:root{
  --blue:#3d67c2;
  --blue-dark:#2f58b4;
  --blue-mid:#4573cc;
  --blue-light:#5e8ce0;
  --text:#444;
  --muted:#666;
  --footer-bg:#f6f7f9;
  --white:#fff;
}
*{box-sizing:border-box;margin:0;padding:0}
html,body{width:1200px;height:2219px;overflow:hidden}
body{position:relative;background:var(--white);font-family:"Open Sans",sans-serif;color:var(--text)}
.abs{position:absolute}
.head{font-family:"Source Sans 3",sans-serif;font-weight:700;color:var(--blue);text-transform:uppercase}

.hero{left:0;top:0;width:1200px;height:680px;background:linear-gradient(180deg,#3f7fd9 0%,#6fa4e3 22%,#4a5c7c 42%,#27334f 70%,#1d2740 100%)}
.brand{left:132px;top:50px;font-family:"Source Sans 3",sans-serif;font-weight:700;font-size:32px;color:var(--white);letter-spacing:.5px}
.nav{left:450px;top:60px;display:flex;gap:0;font-family:"Source Sans 3",sans-serif;font-size:12px;color:var(--white)}
.nav a{color:var(--white);text-decoration:none;position:absolute;white-space:nowrap}
.nav a.active::after{content:"";position:absolute;left:0;right:0;top:27px;height:2px;background:var(--white)}
.hero-title{left:0;width:1200px;top:326px;text-align:center;font-family:"Source Sans 3",sans-serif;font-weight:600;font-size:48px;color:var(--white);letter-spacing:1px}
.hero-sub{left:0;width:1200px;top:394px;text-align:center;font-size:12px;color:#dfe6f2}
.btn{background:var(--blue-mid);color:var(--white);font-family:"Source Sans 3",sans-serif;font-size:13px;text-align:center;border-radius:3px;box-shadow:0 2px 3px rgba(0,0,0,.25)}
.hero-btn{left:524px;top:433px;width:152px;height:41px;line-height:41px}
.dots{left:573px;top:526px;display:flex;gap:6px}
.dots span{width:15px;height:15px;border-radius:50%;background:#d9dde4;border:2px solid #fff}
.dots span:first-child{background:#fff;box-shadow:inset 0 0 0 3px #555}

.features{left:132px;top:590px;width:936px;height:222px;display:flex}
.feature{flex:1;color:var(--white);text-align:center;padding:28px 18px 0}
.feature:nth-child(1){background:var(--blue-dark)}
.feature:nth-child(2){background:var(--blue-mid)}
.feature:nth-child(3){background:var(--blue-light)}
.feature svg{height:56px;width:56px}
.feature h3{font-family:"Source Sans 3",sans-serif;font-weight:600;font-size:19px;margin:10px 0 10px;letter-spacing:.5px}
.feature p{font-size:11px;line-height:19px;color:#dfe7f7;text-align:justify;text-align-last:center}

.who-title{left:0;width:1200px;top:856px;text-align:center;font-size:32px}
.who-text{left:132px;width:936px;top:914px;text-align:center;font-size:11.5px;line-height:19.5px;color:var(--text)}
.who-btn{left:554px;top:998px;width:93px;height:35px;line-height:35px;font-size:12px}

.services{left:0;top:1072px;width:1200px;height:536px;background:linear-gradient(180deg,#f2f3f5 0%,#eceef1 45%,#e8ebe0 75%,#e6e9dc 100%)}
.services-title{left:0;width:1200px;top:1128px;text-align:center;font-size:32px}
.services-sub{left:255px;width:690px;top:1194px;text-align:center;font-size:11.5px;line-height:19px}
.service{width:300px;text-align:center}
.service .disc{width:126px;height:126px;border-radius:50%;background:var(--blue);margin:0 auto;display:flex;align-items:center;justify-content:center}
.service h4{font-family:"Source Sans 3",sans-serif;font-weight:700;font-size:14px;color:var(--blue);margin:25px 0 14px}
.service p{font-size:11.5px;line-height:19px;text-align:justify;text-align-last:center;padding:0 20px}
.service .more{display:block;font-size:11px;color:var(--blue);margin-top:12px}

.usage-title{left:0;width:1200px;top:1656px;text-align:center;font-size:32px}
.tile{top:1728px;width:224px;height:120px}
.tile-label{top:1866px;font-family:"Source Sans 3",sans-serif;font-weight:700;font-size:15px;color:var(--blue);text-transform:uppercase}

.footer{left:0;top:1938px;width:1200px;height:281px;background:var(--footer-bg)}
.foot-brand{left:133px;top:1966px;font-family:"Source Sans 3",sans-serif;font-weight:700;font-size:32px;color:var(--blue)}
.social{left:133px;top:2018px;display:flex;gap:6px}
.social span{width:31px;height:31px;border:1.5px solid #333;border-radius:50%}
.foot-h{font-family:"Source Sans 3",sans-serif;font-weight:700;font-size:13px;color:var(--blue);text-transform:uppercase;top:1970px}
.sitemap{left:440px;top:2009px;font-size:11px;line-height:19.3px;color:var(--muted);list-style:none}
.news-text{left:580px;top:2008px;width:260px;font-size:11px;line-height:25px;color:var(--muted)}
.news-field{left:580px;top:2066px;width:251px;height:34px;border:1px solid #ccc;border-radius:3px;background:#fff;font-size:11px;color:#666;padding:0 14px;line-height:32px}
.news-field svg{position:absolute;right:12px;top:11px}
.contact{left:903px;top:2010px;list-style:none;font-size:11px;color:var(--muted)}
.contact li{display:flex;gap:12px;align-items:flex-start;margin-bottom:7px;line-height:15px}
.contact svg{flex:none;margin-top:2px}
.rule{left:132px;top:2160px;width:936px;height:1px;background:#e0e1e4}
.copy{left:0;width:1200px;top:2176px;text-align:center;font-size:11px;color:#333}
</style>
</head>
<body>

<div class="abs hero" role="img" aria-label="Photo of a worker in a hard hat installing solar panels on a tiled roof under a blue sky"></div>
<div class="abs brand">BRIGHTFIELD HOMES</div>
<nav class="abs nav">
  <a class="active" style="left:0">HOME</a>
  <a style="left:70px">ABOUT US</a>
  <a style="left:158px">SERVICES</a>
  <a style="left:246px">HOW IT WORKS</a>
  <a style="left:358px">BENEFITS</a>
  <a style="left:445px">HOW WE WORK</a>
  <a style="left:558px">CONTACT US</a>
</nav>
<h1 class="abs hero-title">INSTALL SOLAR SYSTEMS</h1>
<p class="abs hero-sub">Help pensioner households to save money and take control of their energy bills</p>
<div class="abs btn hero-btn">REQUEST QUOTE</div>
<div class="abs dots"><span></span><span></span><span></span></div>

<section class="abs features">
  <div class="feature">
    <svg viewBox="0 0 56 56" fill="none" stroke="#fff" stroke-width="2.5"><circle cx="28" cy="14" r="4"/><path d="M28 4v3M20 8l2 2M36 8l-2 2"/><path d="M12 22h32l4 18H8z"/><path d="M10 31h36M20 22l-2 18M28 22v18M36 22l2 18"/><path d="M22 40v6h12v-6"/></svg>
    <h3>SAFE</h3>
    <p>Brightfield Homes is a pioneering approach by councils to support pensioner households to save money and take control of their energy bills by installing</p>
  </div>
  <div class="feature">
    <svg viewBox="0 0 56 56" fill="none" stroke="#fff" stroke-width="2.5"><circle cx="34" cy="34" r="9" fill="#fff"/><path d="M34 19v-4M34 53v-4M19 34h-4M53 34h-4M23 23l-3-3M45 45l3 3M45 23l3-3M23 45l-3 3"/><path d="M10 6v10M18 6v10M7 16h14v6a7 7 0 0 1-14 0zM14 29v8"/></svg>
    <h3>RELIABLE</h3>
    <p>Brightfield Homes is a pioneering approach by councils to support pensioner households to save money and take control of their energy bills by installing</p>
  </div>
  <div class="feature">
    <svg viewBox="0 0 56 56"><circle cx="28" cy="28" r="26" fill="#fff"/><path d="M28 14l11 4v9c0 7-5 12-11 15-6-3-11-8-11-15v-9z" fill="#5e8ce0"/><path d="M23 28l4 4 7-8" stroke="#fff" stroke-width="2.5" fill="none"/></svg>
    <h3>TRUSTWORTHY</h3>
    <p>Brightfield Homes is a pioneering approach by councils to support pensioner households to save money and take control of their energy bills by installing</p>
  </div>
</section>

<h2 class="abs head who-title">WHO WE ARE</h2>
<p class="abs who-text">Brightfield Homes is a pioneering approach by councils to support pensioner households to save money and take control of their energy bills by installing affordable, quality solar systems with no upfront costs. Brightfield Homes is a pioneering approach by Victorian councils to support pensioner households to install solar with no upfront costs. Brightfield Homes is a pioneering approach by Victorian councils to support pensioner households to install solar with no upfront costs.</p>
<div class="abs btn who-btn">Read More</div>

<section class="abs services" role="img" aria-label="Faded photo of a solar panel field on green grass"></section>
<h2 class="abs head services-title">OUR SERVICES</h2>
<p class="abs services-sub">Over 20 Victorian councils have come together with support from the Victorian Government's Clean Power Jobs Fund to run the Brightfield Home program.</p>

<div class="abs service" style="left:117px;top:1263px">
  <div class="disc"><svg width="64" height="64" viewBox="0 0 64 64" fill="#fff"><path d="M32 8L6 30h7v24h18V38h10v16h10V30h7z"/><rect x="30" y="28" width="20" height="24" transform="rotate(-20 40 40)" fill="#fff" stroke="#3d67c2" stroke-width="2"/></svg></div>
  <h4>HOMEOWNERS</h4>
  <p>We are started in support with Victorian councils and four greenhouse alliances to support low income households</p>
  <span class="more">READMORE</span>
</div>
<div class="abs service" style="left:449px;top:1263px">
  <div class="disc"><svg width="70" height="70" viewBox="0 0 70 70" fill="none" stroke="#fff" stroke-width="2.5"><rect x="10" y="10" width="24" height="22"/><path d="M10 21h24M18 10v22M26 10v22M22 32v16"/><path d="M50 12v30M50 22l8-6M50 22l-8-6M50 22l0 -10"/><path d="M12 58c4-10 14-12 22-8 6-8 18-6 22 4v4z" fill="#fff"/></svg></div>
  <h4>PENSION CARD HOLDERS</h4>
  <p>We are started in support with Victorian councils and four greenhouse alliances to support low income households</p>
  <span class="more">READMORE</span>
</div>
<div class="abs service" style="left:778px;top:1263px">
  <div class="disc"><svg width="66" height="66" viewBox="0 0 66 66" fill="none" stroke="#fff" stroke-width="3"><path d="M18 8v52M48 8v52M10 16h16M10 26h16M40 16h16M40 26h16"/><path d="M18 34c10 6 20 6 30 0"/><path d="M34 20l-6 12h8l-6 12" stroke-width="2.5"/></svg></div>
  <h4>HIGH ELECTRICITY USERS</h4>
  <p>We are started in support with Victorian councils and four greenhouse alliances to support low income households</p>
  <span class="more">READMORE</span>
</div>

<h2 class="abs head usage-title">USAGE OF SOLAR</h2>
<div class="abs tile" style="left:132px;background:linear-gradient(135deg,#e9e6e2,#cdc5bc)" role="img" aria-label="Photo of hands holding a glowing light bulb"></div>
<div class="abs tile" style="left:368px;background:linear-gradient(180deg,#3f87d8 0%,#2b4f86 55%,#b85a2e 100%)" role="img" aria-label="Photo of solar panels on a red tiled roof"></div>
<div class="abs tile" style="left:606px;background:linear-gradient(180deg,#8ec6ee 0%,#3c6fb8 55%,#7fb341 100%)" role="img" aria-label="Photo of solar panels in a green field under the sun"></div>
<div class="abs tile" style="left:842px;background:linear-gradient(180deg,#c9dcee 0%,#8b96a4 60%,#4d5a6c 100%)" role="img" aria-label="Photo of two engineers in hard hats beside solar panels"></div>
<div class="abs tile-label" style="left:131px;font-size:17px">REDUCE&nbsp; BILLS</div>
<div class="abs tile-label" style="left:368px;font-size:14px;top:1868px">LIFETIME INVESMENT</div>
<div class="abs tile-label" style="left:611px;font-size:14px;top:1868px">HELP ENVIRONMENT</div>
<div class="abs tile-label" style="left:845px;font-size:14px;top:1870px">EASY TO&nbsp; USE</div>

<footer class="abs footer"></footer>
<div class="abs foot-brand">BRIGHTFIELD HOMES</div>
<div class="abs social"><span></span><span></span><span></span><span></span></div>

<div class="abs foot-h" style="left:440px">SITEMAP</div>
<ul class="abs sitemap">
  <li>Home</li><li>About Us</li><li>Services</li><li>How it Works</li><li>Benefits</li><li>How we work</li>
</ul>

<div class="abs foot-h" style="left:580px">NEWSLETTER</div>
<p class="abs news-text">Enter your email address to receive the latest news and notes from our blog.</p>
<div class="abs news-field">Email Id<svg width="8" height="12" viewBox="0 0 8 12"><path d="M1 1l5 5-5 5" stroke="#555" stroke-width="1.5" fill="none"/></svg></div>

<div class="abs foot-h" style="left:903px">CONTACT US</div>
<ul class="abs contact">
  <li><svg width="12" height="11" viewBox="0 0 12 11" fill="#555"><path d="M1 3c0-2 10-2 10 0v2H8V4H4v1H1z"/><rect x="2" y="6" width="8" height="5" rx="1"/></svg>201-555-0147</li>
  <li><svg width="12" height="11" viewBox="0 0 12 11" fill="#555"><rect x="3" y="0" width="6" height="3"/><rect x="0" y="3" width="12" height="5" rx="1"/><rect x="3" y="7" width="6" height="4"/></svg>201-555-0147</li>
  <li><svg width="12" height="9" viewBox="0 0 12 9" fill="#555"><rect width="12" height="9"/><path d="M0 0l6 5 6-5" stroke="#fff" fill="none"/></svg><span style="text-decoration:underline">info@brightfieldhomes.org</span></li>
  <li><svg width="12" height="14" viewBox="0 0 12 14" fill="#555"><path d="M6 0a5 5 0 0 1 5 5c0 4-5 9-5 9S1 9 1 5a5 5 0 0 1 5-5z"/><circle cx="6" cy="5" r="2" fill="#f6f7f9"/></svg><span>#2868 Lorem ipsum dolor sit<br>amet, consectetur</span></li>
</ul>

<div class="abs rule"></div>
<p class="abs copy">2017 © Brightfield Homes. All Right Reserved.</p>

</body>
</html>
```